Business Cards for a law firm

Business cards for our law firm. Use our silhoette logo and OAK PARTNERS - check our website (www.oakpartners.example)

Contact Information for Business Card

our silhouette logo, OAK PARTNERS, 800-555-0147, Dorian Pemberton, dorian@oakpartners.example

Requirements
Must have
• our silhouette logo, OAK PARTNERS, 800-555-0147, Dorian Pemberton, dorian@oakpartners.example

```html
<!DOCTYPE html>
<html lang="en">
<head>
<meta charset="UTF-8">
<title>Oak Partners – Business Cards</title>
<link rel="stylesheet" href="https://fonts.googleapis.com/css2?family=Montserrat:wght@400;500;700&display=swap">
<style>
  :root {
    --navy: #1f2f6b;
    --navy-deep: #1b295e;
    --navy-soft: #2a3c7e;
    --paper: #ffffff;
    --paper-shade: #eeeff1;
    --backdrop: #e6e4e0;
  }
  * { box-sizing: border-box; margin: 0; padding: 0; }
  html, body { width: 1200px; height: 900px; overflow: hidden; }
  body {
    background: var(--backdrop);
    font-family: "Montserrat", sans-serif;
    display: flex;
    flex-direction: column;
    align-items: center;
    justify-content: center;
    gap: 40px;
  }
  .card {
    width: 680px;
    height: 388px;
    border-radius: 22px;
    position: relative;
    overflow: hidden;
    box-shadow: 0 6px 18px rgba(0,0,0,0.15);
  }
  /* Front */
  .card-front {
    background: linear-gradient(180deg, var(--paper) 0%, var(--paper-shade) 100%);
    color: var(--navy);
  }
  .brand {
    position: absolute;
    top: 62px;
    left: 128px;
    display: flex;
    align-items: center;
    gap: 18px;
  }
  .brand-mark {
    width: 40px;
    height: 40px;
    background: var(--navy);
  }
  .brand-name {
    font-weight: 700;
    font-size: 46px;
    letter-spacing: 3px;
    color: var(--navy);
  }
  .person {
    position: absolute;
    top: 168px;
    left: 128px;
    width: 228px;
    text-align: right;
  }
  .person-name {
    font-weight: 700;
    font-size: 20px;
    letter-spacing: 1.5px;
    white-space: nowrap;
  }
  .person-title {
    font-weight: 500;
    font-size: 13px;
    letter-spacing: 1.5px;
    margin-top: 2px;
  }
  .divider {
    position: absolute;
    left: 382px;
    top: 150px;
    width: 3px;
    height: 88px;
    background: var(--navy);
  }
  .contacts {
    position: absolute;
    left: 408px;
    top: 150px;
    list-style: none;
    display: flex;
    flex-direction: column;
    gap: 12px;
  }
  .contacts li {
    display: flex;
    align-items: center;
    gap: 12px;
    font-size: 15px;
    letter-spacing: 0.6px;
    color: #222a44;
  }
  .contacts svg { width: 14px; height: 14px; fill: var(--navy); flex: none; }
  .address-band {
    position: absolute;
    left: 0; right: 0;
    top: 270px;
    height: 30px;
    background: var(--navy);
    color: var(--paper);
    font-size: 14px;
    font-weight: 500;
    letter-spacing: 1px;
    display: flex;
    align-items: center;
    justify-content: center;
  }
  .accent-stripe {
    position: absolute;
    left: 0; right: 0;
    top: 326px;
    height: 20px;
    background: var(--navy);
  }
  /* Back */
  .card-back {
    background: linear-gradient(160deg, var(--navy-soft) 0%, var(--navy-deep) 100%);
    display: flex;
    align-items: center;
    justify-content: center;
  }
  .back-brand {
    font-weight: 700;
    font-size: 52px;
    letter-spacing: 4px;
    color: #33468a;
  }
</style>
</head>
<body>
  <section class="card card-front" aria-label="Business card front">
    <div class="brand">
      <span class="brand-mark" aria-hidden="true"></span>
      <span class="brand-name">OAK PARTNERS</span>
    </div>
    <div class="person">
      <p class="person-name">DORIAN PEMBERTON</p>
      <p class="person-title">OWNER</p>
    </div>
    <div class="divider" aria-hidden="true"></div>
    <ul class="contacts">
      <li>
        <svg viewBox="0 0 24 24" aria-hidden="true"><path d="M6.6 10.8a15.1 15.1 0 0 0 6.6 6.6l2.2-2.2c.3-.3.7-.4 1-.2 1.1.4 2.3.6 3.6.6.6 0 1 .4 1 1V20c0 .6-.4 1-1 1C10.6 21 3 13.4 3 4c0-.6.4-1 1-1h3.5c.6 0 1 .4 1 1 0 1.3.2 2.5.6 3.6.1.3 0 .7-.2 1z"/></svg>
        800-555-0147
      </li>
      <li>
        <svg viewBox="0 0 24 24" aria-hidden="true"><path d="M2 5h20v14H2z M4 7v.4l8 5 8-5V7l-8 5z" fill-rule="evenodd"/></svg>
        dorian@oakpartners.example
      </li>
      <li>
        <svg viewBox="0 0 24 24" aria-hidden="true"><path d="M12 2a10 10 0 1 0 0 20 10 10 0 0 0 0-20zm6.9 6h-3a15.6 15.6 0 0 0-1.3-3.9A8 8 0 0 1 18.9 8zM12 4c.8 1.2 1.5 2.5 1.9 4h-3.8c.4-1.5 1.1-2.8 1.9-4zM4.3 14a8.2 8.2 0 0 1 0-4h3.4a16.5 16.5 0 0 0 0 4zm.8 2h3a15.6 15.6 0 0 0 1.3 3.9A8 8 0 0 1 5.1 16zm3-8h-3a8 8 0 0 1 4.3-3.9A15.6 15.6 0 0 0 8.1 8zM12 20c-.8-1.2-1.5-2.5-1.9-4h3.8c-.4 1.5-1.1 2.8-1.9 4zm2.3-6H9.7a14.7 14.7 0 0 1 0-4h4.6a14.7 14.7 0 0 1 0 4zm.3 5.9a15.6 15.6 0 0 0 1.3-3.9h3a8 8 0 0 1-4.3 3.9zm1.7-5.9a16.5 16.5 0 0 0 0-4h3.4a8.2 8.2 0 0 1 0 4z"/></svg>
        www.oakpartners.example
      </li>
    </ul>
    <div class="address-band">1450 Harbor Lane #310, Fairview Hills, CA 90000</div>
    <div class="accent-stripe" aria-hidden="true"></div>
  </section>

  <section class="card card-back" aria-label="Business card back">
    <span class="back-brand">OAK PARTNERS</span>
  </section>
</body>
</html>
```